Business Cards - New Logo Rebranding

Hello We know have a red and blue logo and are looking to create new cards. We are looking for the best creativity of the new logo merged with some of the existing artwork provided.

Target Market(s)

Realtors

Industry/Entity Type

Real Estate

Contact Information for Business Card

New logo with rebranded colors

Requirements
Must have
• Creative use of the new logo

```html
<!DOCTYPE html>
<html lang="en">
<head>
<meta charset="utf-8">
<title>Summit Crest Business Cards</title>
<link rel="stylesheet" href="https://fonts.googleapis.com/css2?family=Montserrat:wght@400;500;600;700;800&display=swap">
<style>
  :root {
    --brand-blue: #1f6fc5;
    --brand-blue-deep: #1459a8;
    --brand-blue-light: #3b8ad6;
    --brand-red: #e0343b;
    --ink: #3a3a3a;
    --paper: #ffffff;
    --stage: #e9ebee;
    --badge-gold: #c9a646;
    --badge-silver: #b9b6a6;
  }
  * { box-sizing: border-box; margin: 0; padding: 0; }
  html, body { width: 1200px; height: 912px; overflow: hidden; }
  body {
    background: var(--stage);
    font-family: "Montserrat", Arial, sans-serif;
    position: relative;
  }
  .card {
    position: absolute;
    width: 640px;
    height: 366px;
    border-radius: 18px;
    overflow: hidden;
    box-shadow: 0 10px 28px rgba(0,0,0,0.18);
  }

  /* ---------- back side ---------- */
  .card-back {
    left: 60px; top: 60px;
    background: linear-gradient(135deg, var(--brand-blue-deep) 0%, var(--brand-blue) 55%, var(--brand-blue-light) 100%);
    color: var(--paper);
  }
  .headline {
    position: absolute; left: 36px; right: 30px; top: 32px;
    font-weight: 800; font-size: 25px; letter-spacing: 0.2px;
    white-space: nowrap;
  }
  .divider-rule {
    position: absolute; left: 0; right: 0; top: 93px;
    height: 3px; background: var(--brand-red);
  }
  .why-pill {
    position: absolute; left: 150px; top: 78px;
    background: var(--brand-red);
    border-radius: 20px;
    padding: 6px 26px;
    font-weight: 700; font-size: 19px;
  }
  .feature-list {
    position: absolute; top: 132px;
    list-style: none;
    font-weight: 600; font-size: 15px; line-height: 1.3;
  }
  .feature-list li { position: relative; padding-left: 16px; margin-bottom: 7px; }
  .feature-list li::before {
    content: ""; position: absolute; left: 0; top: 8px;
    width: 5px; height: 5px; border-radius: 50%; background: var(--brand-red);
  }
  .feature-list.col-left { left: 36px; width: 300px; }
  .feature-list.col-right { left: 340px; width: 285px; }
  .badge-row {
    position: absolute; left: 300px; bottom: 22px;
    display: flex; align-items: center; gap: 10px;
  }
  .badge { width: 34px; height: 34px; border-radius: 50%; }
  .badge.red-ring { background: #f2f2f2; border: 3px solid var(--brand-red); }
  .badge.gold { background: var(--badge-gold); border: 3px solid #e6cf7e; }
  .badge.silver { background: var(--badge-silver); border: 3px solid #ddd9c8; }
  .badge-sep { width: 2px; height: 30px; background: var(--brand-red); margin: 0 4px; }
  .badge.wide { width: 64px; height: 26px; border-radius: 13px; background: #2b3e8f; border: 2px solid var(--badge-gold); }
  .listing-name { font-weight: 700; font-size: 13px; display: flex; align-items: center; gap: 4px; }
  .listing-dot { width: 12px; height: 12px; border-radius: 50%; background: var(--paper); }

  /* ---------- front side ---------- */
  .card-front { left: 500px; top: 486px; background: var(--paper); }
  .portrait {
    position: absolute; right: 0; top: 0; bottom: 0; width: 215px;
    background: linear-gradient(160deg, #f3f5f8 0%, #c9a58c 30%, #2c5fc0 55%, #1f4fae 100%);
  }
  .brand {
    position: absolute; left: 34px; top: 34px;
    display: flex; align-items: center; gap: 10px;
  }
  .brand-mark { width: 42px; height: 42px; border-radius: 50%; background: var(--brand-red); }
  .brand-name { font-weight: 800; font-size: 27px; color: var(--brand-blue); letter-spacing: 0.5px; }
  .brand-tagline {
    position: absolute; left: 86px; top: 72px;
    font-weight: 600; font-size: 9px; color: var(--brand-blue); letter-spacing: 1px;
  }
  .person-name {
    position: absolute; left: 34px; top: 104px;
    font-weight: 800; font-size: 28px; letter-spacing: 0.3px;
  }
  .person-name .first { color: var(--brand-blue); }
  .person-name .last { color: var(--brand-red); }
  .person-role {
    position: absolute; left: 34px; top: 140px;
    font-weight: 500; font-size: 17px; color: var(--ink);
  }
  .accent-dash { position: absolute; left: 34px; width: 22px; height: 3px; background: var(--brand-red); }
  .accent-dash.top { top: 172px; }
  .accent-dash.bottom { top: 312px; }
  .contact-list {
    position: absolute; left: 34px; top: 184px;
    list-style: none;
    font-weight: 500; font-size: 15.5px; color: var(--ink);
  }
  .contact-list li { display: flex; align-items: center; gap: 12px; height: 29px; }
  .contact-list svg { width: 17px; height: 17px; flex: none; }
  .service-line {
    position: absolute; left: 34px; top: 323px;
    font-weight: 500; font-size: 13px; color: var(--ink);
    white-space: nowrap;
  }
  .service-line .sep { color: var(--brand-red); margin: 0 4px; }
</style>
</head>
<body>

<section class="card card-back" aria-label="Card back">
  <h1 class="headline">CALIFORNIA'S #1 INSPECTION COMPANY!</h1>
  <div class="divider-rule"></div>
  <div class="why-pill">Why Choose Summit Crest</div>

  <ul class="feature-list col-left">
    <li>Performing Inspections Since 1984</li>
    <li>HomeCert Certified Master / Professional Inspectors®</li>
    <li>500,000+ Inspections Completed Statewide</li>
    <li>90-Day Inspection Guarantees</li>
  </ul>
  <ul class="feature-list col-right">
    <li>Request of Repairs Pricer Report</li>
    <li>Aviation Board Drone Licensed Roof Inspectors upon request</li>
    <li>5,000+ 5-Star Reviews on Searchly &amp; Reviewly</li>
  </ul>

  <div class="badge-row">
    <div class="badge red-ring"></div>
    <div class="badge gold"></div>
    <div class="badge silver"></div>
    <div class="badge-sep"></div>
    <div class="badge wide"></div>
    <div class="listing-name">Reviewly</div>
    <div class="listing-name"><span class="listing-dot"></span></div>
  </div>
</section>

<section class="card card-front" aria-label="Card front">
  <div class="portrait" role="img" aria-label="Portrait photo of the inspector in a blue company polo shirt"></div>

  <div class="brand">
    <span class="brand-mark"></span>
    <span class="brand-name">SUMMIT CREST</span>
  </div>
  <div class="brand-tagline">INSPECTION PROFESSIONALS</div>

  <h2 class="person-name"><span class="first">DANA</span> <span class="last">WHITCOMB</span></h2>
  <p class="person-role">Certified Mold Inspector</p>

  <div class="accent-dash top"></div>
  <ul class="contact-list">
    <li>
      <svg viewBox="0 0 24 24" fill="var(--brand-blue)"><path d="M6.6 10.8a15.1 15.1 0 0 0 6.6 6.6l2.2-2.2c.3-.3.7-.4 1-.2 1.1.4 2.3.6 3.6.6.6 0 1 .4 1 1V20c0 .6-.4 1-1 1A17 17 0 0 1 3 4c0-.6.4-1 1-1h3.5c.6 0 1 .4 1 1 0 1.3.2 2.5.6 3.6.1.3 0 .7-.2 1z"/></svg>
      800.555.0142
    </li>
    <li>
      <svg viewBox="0 0 24 24" fill="none" stroke="var(--brand-blue)" stroke-width="2"><rect x="6" y="2" width="12" height="20" rx="2"/><line x1="11" y1="18" x2="13" y2="18"/></svg>
      562.555.0199
    </li>
    <li>
      <svg viewBox="0 0 24 24" fill="var(--brand-blue)"><path d="M2 5h20v14H2z"/><path d="M2 5l10 8 10-8" fill="none" stroke="#fff" stroke-width="1.8"/></svg>
      dana@summitcrestinspect.com
    </li>
    <li>
      <svg viewBox="0 0 24 24" fill="none" stroke="var(--brand-blue)" stroke-width="1.8"><circle cx="12" cy="12" r="9.5"/><ellipse cx="12" cy="12" rx="4" ry="9.5"/><line x1="2.5" y1="12" x2="21.5" y2="12"/><line x1="4" y1="7" x2="20" y2="7"/><line x1="4" y1="17" x2="20" y2="17"/></svg>
      www.SummitCrestInspect.com
    </li>
  </ul>
  <div class="accent-dash bottom"></div>
  <p class="service-line">Home<span class="sep">•</span>Sewer<span class="sep">•</span>Mold<span class="sep">•</span>Commercial<span class="sep">•</span>Termite<span class="sep">•</span>Roof</p>
</section>

</body>
</html>
```